Veltrane Group Business Card Design

The CEO is looking for a new trendy look for his business card.
You can stay with current branding or come up with something new/creative. It can be 3D, including Medical Office buildings. You can use our logo in a variety of colors. Please include name, title, company name, company website, email address, cell number

Target Market(s)

Real Estate Development and Construction

Industry/Entity Type

Health care real estate

Contact Information for Business Card

Rohesh Kamdar, CEO M-604.781.2249 E-roheshkamdar@veltrane.com Address:4180 Lindqvist Ave, Tampa, FL 33482 www.veltrane.com

Font styles to use
Other font styles liked:
• Be creative

Requirements
Must have
• Creative, trendy look
Nice to have
• Please go to our website to get a feel- www. veltrane.com
Should not have
• small fonts

```html
<!DOCTYPE html>
<html lang="en">
<head>
<meta charset="utf-8">
<title>Veltrane Group Business Card</title>
<link rel="stylesheet" href="https://fonts.googleapis.com/css2?family=Arimo:wght@400;700&display=swap">
<style>
  :root {
    --brand-red: #b21f2b;
    --brand-navy: #1d2b52;
    --paper: #ffffff;
    --backdrop: #e6e6e8;
    --muted-navy: #3a4466;
  }
  * { margin: 0; padding: 0; box-sizing: border-box; }
  html, body { width: 1200px; height: 874px; overflow: hidden; }
  body {
    background: var(--backdrop);
    font-family: "Arimo", Arial, sans-serif;
    position: relative;
  }
  .card {
    position: absolute;
    left: 290px;
    width: 620px;
    height: 354px;
    border-radius: 22px;
    overflow: hidden;
    box-shadow: 0 10px 26px rgba(0,0,0,0.18);
  }
  .card-front { top: 46px; background: var(--brand-red); }
  .card-back { top: 474px; background: var(--paper); }

  .wordmark {
    position: absolute;
    font-weight: 700;
    letter-spacing: -2px;
    line-height: 1;
    white-space: nowrap;
  }
  .card-front .wordmark {
    color: var(--paper);
    font-size: 82px;
    left: 0; right: 0;
    top: 118px;
    text-align: center;
  }
  .front-url {
    position: absolute;
    left: 0; right: 0;
    bottom: 34px;
    text-align: center;
    color: var(--paper);
    font-size: 15px;
  }

  .back-art { position: absolute; inset: 0; }
  .card-back .wordmark {
    color: var(--brand-red);
    font-size: 50px;
    left: 40px;
    top: 120px;
  }
  .holder {
    position: absolute;
    right: 40px;
    top: 50px;
    text-align: right;
  }
  .holder-name {
    color: var(--brand-red);
    font-weight: 700;
    font-size: 27px;
  }
  .holder-title {
    color: var(--muted-navy);
    font-size: 15px;
    margin-top: 4px;
  }
  .contact {
    position: absolute;
    right: 32px;
    bottom: 18px;
    text-align: right;
    color: var(--paper);
    font-size: 15px;
    line-height: 1.3;
  }
  .contact-address { margin-bottom: 6px; padding-right: 24px; }
  .contact-row { display: flex; justify-content: flex-end; align-items: center; gap: 8px; }
  .contact-row svg { width: 16px; height: 16px; flex: none; }
</style>
</head>
<body>

<section class="card card-front" aria-label="Card front">
  <div class="wordmark">Veltrane Group</div>
  <div class="front-url">www.veltrane.com</div>
</section>

<section class="card card-back" aria-label="Card back">
  <svg class="back-art" viewBox="0 0 620 354" preserveAspectRatio="none" aria-hidden="true">
    <path d="M0,215 Q280,300 620,110 L620,354 L0,354 Z" fill="var(--brand-red)"/>
    <path d="M0,207 Q280,292 620,103" fill="none" stroke="var(--brand-navy)" stroke-width="3"/>
    <path d="M0,201 Q280,286 620,98" fill="none" stroke="#c9ccd6" stroke-width="1.5"/>
  </svg>

  <div class="wordmark">Veltrane Group</div>

  <div class="holder">
    <div class="holder-name">Rohesh Kamdar</div>
    <div class="holder-title">CEO</div>
  </div>

  <div class="contact">
    <div class="contact-address">4180 Lindqvist Ave, Tampa<br>FL 33482</div>
    <div class="contact-row">604.781.2249
      <svg viewBox="0 0 16 16" aria-hidden="true"><path fill="#fff" d="M3.6 1.5l2.3 2.6-1.3 1.8c.9 2 2.6 3.7 4.6 4.6l1.8-1.3 2.6 2.3-1.2 2.2C7.6 15.3.7 8.4 1.4 2.7z"/></svg>
    </div>
    <div class="contact-row">roheshkamdar@veltrane.com
      <svg viewBox="0 0 16 16" aria-hidden="true"><rect x="1.5" y="3.5" width="13" height="9" fill="#fff"/><path d="M1.5 3.5L8 9l6.5-5.5" fill="none" stroke="var(--brand-red)" stroke-width="1.2"/></svg>
    </div>
    <div class="contact-row">www.veltrane.com
      <svg viewBox="0 0 16 16" aria-hidden="true"><circle cx="8" cy="8" r="6.5" fill="#fff"/><path d="M1.5 8h13M8 1.5c-2.5 3-2.5 10 0 13M8 1.5c2.5 3 2.5 10 0 13" fill="none" stroke="var(--brand-red)" stroke-width="1"/></svg>
    </div>
  </div>
</section>

</body>
</html>
```